Detail Shop Business card design

i need a business card design for my new detailing company called 'Brisk's Polish Works'. i want an all black and white design . simple, direct and to the point. i want the designer to choose a fitting font to match the logothe front should have logo, address, phone and email and the back side should have a slogan and text indicating that we offer services on anything including cars, trucks, motorcycles and RVs. slogan will read "we take pride in your ride"
maybe also very small on the back side the IG icon with Brisks_Polish_Works

phone 208.417.6352
address 3847 E Larkin Ave
Spokane WA 99214
email: BrisksPolish@mailvexo.com

Target Market(s)

all ages , auto enthusiasts

Industry/Entity Type

Automotive

Contact Information for Business Card

the front should have logo, address, phone and email and the back side should have a slogan and text indicating that we offer services on anything including cars, trucks, motorcycles and RVs. slogan will read "we take pride in your ride"

phone 208.417.6352
address 3847 E Larkin Ave
Spokane WA 99214

Colors
000000
ffffff

Requirements
Must have
• bold font and very simple design with good spacing
Nice to have
• anything creative from the designer indicating we service any types of vehicles
Should not have
• any colors ,

```html
<!DOCTYPE html>
<html lang="en">
<head>
<meta charset="utf-8">
<title>Brisk's Polish Works – Business Card</title>
<link rel="stylesheet" href="https://fonts.googleapis.com/css2?family=Roboto:wght@400;500;700&family=Roboto+Condensed:wght@400&family=Archivo:wght@700&display=swap">
<style>
  :root {
    --ink: #000000;
    --card-dark: #1b1b1c;
    --card-light: #f6f6f6;
    --paper: #ffffff;
    --backdrop: #e6e6e6;
    --text-soft: #ececec;
  }
  html, body {
    margin: 0;
    padding: 0;
    width: 1200px;
    height: 960px;
    overflow: hidden;
    background: var(--backdrop);
  }
  .stage {
    position: relative;
    width: 1200px;
    height: 960px;
  }
  .card {
    position: absolute;
    width: 600px;
    height: 342px;
    box-shadow: 0 2px 6px rgba(0,0,0,0.25);
  }

  /* Front */
  .card-front {
    left: 314px;
    top: 113px;
    background: var(--card-dark);
    color: var(--text-soft);
    font-family: "Roboto", Arial, sans-serif;
  }
  .identity {
    position: absolute;
    right: 351px;
    top: 152px;
    text-align: right;
  }
  .identity-name {
    margin: 0;
    font-weight: 500;
    font-size: 20px;
    line-height: 24px;
    color: var(--paper);
  }
  .identity-role {
    margin: 0;
    font-size: 14px;
    line-height: 20px;
  }
  .divider {
    position: absolute;
    left: 271px;
    top: 132px;
    width: 2px;
    height: 80px;
    background: var(--text-soft);
  }
  .contact-list {
    position: absolute;
    left: 290px;
    top: 135px;
    margin: 0;
    padding: 0;
    list-style: none;
  }
  .contact-list li {
    display: flex;
    align-items: center;
    height: 19px;
    font-size: 14px;
  }
  .contact-list svg, .address svg {
    width: 13px;
    height: 13px;
    margin-right: 10px;
    fill: var(--paper);
    flex: none;
  }
  .address {
    position: absolute;
    left: 0;
    right: 0;
    top: 278px;
    display: flex;
    justify-content: center;
    align-items: center;
    font-size: 14px;
  }

  /* Back */
  .card-back {
    left: 311px;
    top: 472px;
    background: var(--card-light);
    color: var(--ink);
  }
  .brand {
    position: absolute;
    left: 0;
    right: 0;
    top: 125px;
    display: flex;
    justify-content: center;
    align-items: center;
    gap: 14px;
  }
  .brand-dot {
    width: 40px;
    height: 40px;
    border-radius: 50%;
    background: var(--ink);
  }
  .brand-name {
    font-family: "Roboto", Arial, sans-serif;
    font-weight: 700;
    font-size: 30px;
    color: var(--ink);
  }
  .slogan {
    position: absolute;
    left: 137px;
    width: 324px;
    top: 271px;
    margin: 0;
    padding-bottom: 4px;
    border-bottom: 1.5px solid var(--ink);
    text-align: center;
    font-family: "Archivo", Arial, sans-serif;
    font-weight: 700;
    font-size: 17px;
    line-height: 20px;
    text-transform: uppercase;
  }
  .services {
    position: absolute;
    left: 0;
    right: 0;
    top: 298px;
    margin: 0;
    text-align: center;
    font-family: "Roboto Condensed", Arial, sans-serif;
    font-size: 14px;
  }
</style>
</head>
<body>
<main class="stage">
  <section class="card card-front" aria-label="Card front">
    <div class="identity">
      <p class="identity-name">DALE MERCER</p>
      <p class="identity-role">CEO/FOUNDER</p>
    </div>
    <div class="divider"></div>
    <ul class="contact-list">
      <li>
        <svg viewBox="0 0 24 24" aria-hidden="true"><path d="M6.6 10.8a15.1 15.1 0 0 0 6.6 6.6l2.2-2.2c.3-.3.7-.4 1-.2 1.1.4 2.3.6 3.6.6.6 0 1 .4 1 1V20c0 .6-.4 1-1 1A17 17 0 0 1 3 4c0-.6.4-1 1-1h3.5c.6 0 1 .4 1 1 0 1.3.2 2.5.6 3.6.1.3 0 .7-.2 1z"/></svg>
        208.417.6352
      </li>
      <li>
        <svg viewBox="0 0 24 24" aria-hidden="true"><path d="M7 1h10a2 2 0 0 1 2 2v18a2 2 0 0 1-2 2H7a2 2 0 0 1-2-2V3a2 2 0 0 1 2-2zm0 3v14h10V4zm5 15.5a1.2 1.2 0 1 0 0 2.4 1.2 1.2 0 0 0 0-2.4z"/></svg>
        836 215 4870
      </li>
      <li>
        <svg viewBox="0 0 24 24" aria-hidden="true"><path d="M2 5h20v14H2zm2 2v.5l8 5 8-5V7zm0 2.8V17h16V9.8l-8 5z"/></svg>
        BrisksPolish@mailvexo.com
      </li>
      <li>
        <svg viewBox="0 0 24 24" aria-hidden="true"><path d="M12 2a10 10 0 1 0 0 20 10 10 0 0 0 0-20zm-1 17.9A8 8 0 0 1 4.2 10L9 14.8v1a2 2 0 0 0 2 2zm6.9-2.5A2 2 0 0 0 16 16h-1v-3a1 1 0 0 0-1-1H8v-2h2a1 1 0 0 0 1-1V7h2a2 2 0 0 0 2-2v-.4a8 8 0 0 1 2.9 12.8z"/></svg>
        www.briskspolishworks.com
      </li>
    </ul>
    <p class="address">
      <svg viewBox="0 0 24 24" aria-hidden="true"><path d="M12 2a7 7 0 0 0-7 7c0 5.2 7 13 7 13s7-7.8 7-13a7 7 0 0 0-7-7zm0 9.5a2.5 2.5 0 1 1 0-5 2.5 2.5 0 0 1 0 5z"/></svg>
      3847 E Larkin Ave Spokane WA 99214
    </p>
  </section>

  <section class="card card-back" aria-label="Card back">
    <div class="brand">
      <span class="brand-dot" aria-hidden="true"></span>
      <span class="brand-name">Brisk's Polish Works</span>
    </div>
    <h2 class="slogan">We take pride in your ride</h2>
    <p class="services">we offer services on anything including cars, trucks, motorcycles &amp; RVs</p>
  </section>
</main>
</body>
</html>
```